Website design for an Italian restaurant in Amsterdam

I need a design for a client of mine. It is for Teatro Lucerna, an Italian restaurant in Amsterdam.
We are going for a clean, modern look but we also need to realise an authentic feel.
The restaurant is located in an old movie theatre, that is where the name Teatro Lucerna comes from.
Industry/Entity Type
Italian Restaurant
Number of Pages Required
1 page
Font styles to use
Sans Serif
Colors
Designer to choose colors to be used in the design.

```html
<!DOCTYPE html>
<html lang="en">
<head>
<meta charset="utf-8">
<title>Teatro Lucerna – Italian restaurant Amsterdam</title>
<link rel="stylesheet" href="https://fonts.googleapis.com/css2?family=Raleway:wght@500;600;700;800&family=Open+Sans:wght@400;600;700&display=swap">
<style>
:root{
  --wine:#a14a5c;
  --wine-dark:#8e3e4f;
  --ink:#1c1c1c;
  --text:#555;
  --light:#f1f1f1;
  --white:#fff;
  --night:#1d1512;
  --head:"Raleway",sans-serif;
  --body:"Open Sans",sans-serif;
}
*{box-sizing:border-box;margin:0;padding:0}
html,body{width:1200px;height:3066px;overflow:hidden}
body{position:relative;font-family:var(--body);color:var(--text);background:var(--white)}
section,header{position:absolute;left:0;width:1200px}

/* hero */
.hero{top:0;height:645px;overflow:hidden}
.hero-photo{position:absolute;inset:0;background:linear-gradient(100deg,#3e281b 0%,#5a3a27 45%,#6a4630 70%,#4e3322 100%)}
.hero-panel{position:absolute;left:98px;top:0;width:337px;height:645px;background:rgba(10,6,4,.72)}
.brand{position:absolute;left:140px;top:52px;display:flex;align-items:center;gap:10px;color:var(--white)}
.brand-dot{width:28px;height:28px;border-radius:50%;background:var(--wine)}
.brand-name{font-family:var(--body);font-size:21px;font-weight:600;letter-spacing:.5px}
.brand-sub{position:absolute;left:178px;top:82px;font-size:10px;color:#d9a3ae}
.top-contact{position:absolute;right:62px;top:30px;display:flex;align-items:center;gap:26px;color:var(--white);font-weight:700;font-size:18px}
.top-contact .phone{display:flex;align-items:center;gap:8px}
.menu-btn{width:48px;height:48px;border:2px solid var(--white);border-radius:50%;display:flex;align-items:center;justify-content:center}
.hero-title{position:absolute;left:135px;top:178px;font-family:var(--head);font-weight:800;font-size:49px;line-height:64px;color:var(--white)}
.hero-lead{position:absolute;left:137px;top:325px;width:280px;font-size:19px;line-height:32px;color:var(--white)}
.btn-outline{display:inline-flex;align-items:center;justify-content:center;border:2px solid var(--white);border-radius:30px;color:var(--white);font-family:var(--head);font-weight:700;text-transform:uppercase}
.hero .btn-outline{position:absolute;left:137px;top:426px;width:206px;height:58px;font-size:17px}
.dots{position:absolute;left:568px;top:576px;display:flex;gap:3px}
.dots span{width:13px;height:13px;border:2px solid var(--white);border-radius:50%}
.dots span:first-child{background:var(--white)}

/* banner */
.announce{top:645px;height:73px;background:var(--wine);color:var(--white);display:flex;align-items:center;justify-content:center;font-family:var(--head);font-weight:800;font-size:31px}

/* story */
.story{top:718px;height:574px}
.story-text{position:absolute;left:98px;top:132px;width:430px;text-align:center}
.kicker{font-family:var(--head);font-weight:700;font-size:21px;color:var(--ink)}
.section-title{font-family:var(--head);font-weight:700;color:var(--ink)}
.story .section-title{font-size:38px;margin-top:4px}
.story p{font-size:13px;line-height:28px;margin-top:18px}
.btn-solid{display:inline-flex;align-items:center;justify-content:center;background:var(--wine);color:var(--white);border-radius:30px;font-family:var(--head);font-weight:700;text-transform:uppercase;font-size:15px}
.story .btn-solid{width:151px;height:51px;margin-top:36px}
.photo{position:absolute;top:83px;width:159px;height:397px}
.photo-a{left:605px;background:linear-gradient(180deg,#2a1d18,#a0522d 45%,#6b4a2a)}
.photo-b{left:773px;background:linear-gradient(180deg,#3a2c24,#140f0d 40%,#4d3e30)}
.photo-c{left:941px;background:linear-gradient(180deg,#2f2a26,#b8432c 45%,#d8d2c8)}

/* about */
.about{top:1292px;height:527px;background:var(--light)}
.about-card{position:absolute;left:98px;top:63px;width:1004px;height:399px;background:var(--white);box-shadow:0 0 4px rgba(0,0,0,.15);padding:4px}
.about-photo{position:absolute;left:4px;top:4px;width:417px;height:391px;background:linear-gradient(135deg,#d9d7cf,#7a6a4a 45%,#6e8a3a 70%,#e6e3d8)}
.about-body{position:absolute;left:460px;top:40px;width:515px}
.about .section-title{font-size:38px}
.about p{font-size:12.5px;line-height:24px;margin-top:20px}
.about .btn-solid{width:151px;height:51px;margin-top:24px}

/* menu */
.menu{top:1819px;height:450px}
.menu .section-title{position:absolute;top:92px;width:100%;text-align:center;font-size:38px}
.menu-card{position:absolute;top:178px;width:480px;height:180px;background:var(--white);box-shadow:0 0 4px rgba(0,0,0,.18)}
.menu-card.left{left:98px}.menu-card.right{left:620px}
.menu-photo{position:absolute;left:0;top:0;width:188px;height:180px}
.left .menu-photo{background:linear-gradient(135deg,#f2efe8,#b33a26 50%,#7a2a1a)}
.right .menu-photo{background:linear-gradient(135deg,#3a6a2a,#8ab04a 45%,#f3eee4 70%,#c0392b)}
.menu-card h3{position:absolute;left:222px;top:28px;font-family:var(--head);font-weight:700;font-size:18px;color:var(--ink)}
.menu-card ul{position:absolute;left:222px;top:63px;list-style:none}
.menu-card li{display:flex;align-items:center;gap:10px;font-size:13.5px;line-height:26px}

/* features */
.features{top:2269px;height:212px;background:var(--wine);color:var(--white)}
.feature{position:absolute;top:0;width:368px;height:212px}
.feature:nth-child(1){left:98px}.feature:nth-child(2){left:461px}.feature:nth-child(3){left:832px}
.divider{position:absolute;top:32px;width:1px;height:148px;background:rgba(255,255,255,.35)}
.feature-icon{position:absolute;left:2px;top:22px;width:86px;height:86px;border-radius:50%;background:var(--white);display:flex;align-items:center;justify-content:center}
.feature h3{position:absolute;left:110px;top:24px;font-family:var(--head);font-weight:700;font-size:24px}
.feature p{position:absolute;left:110px;top:62px;width:220px;font-size:13.5px;line-height:22px}
.feature .btn-outline{position:absolute;left:112px;top:125px;width:160px;height:42px;font-size:13px}

/* contact */
.contact{top:2481px;height:585px;background:radial-gradient(circle at 30% 40%,#3a2a22,#1d1512 60%),var(--night);color:var(--white)}
.contact .section-title{position:absolute;top:72px;width:100%;text-align:center;color:var(--white);font-size:35px}
.col-title{position:absolute;font-family:var(--head);font-weight:700;font-size:15px;text-transform:uppercase}
.field-label{position:absolute;font-size:11px;text-transform:uppercase}
.field{position:absolute;background:var(--white);border-radius:2px}
.submit{position:absolute;left:630px;top:426px;width:100px;height:34px;font-size:13px}
.info-item{position:absolute;left:809px;display:flex;align-items:center;gap:18px;font-size:12px;line-height:20px}
.info-icon{width:36px;height:36px;border-radius:50%;border:2px solid var(--white);display:flex;align-items:center;justify-content:center;flex:none}
.hours{position:absolute;left:809px;top:399px;width:290px;font-size:12px}
.hours div{display:flex;height:25.5px}
.hours span:first-child{width:197px}
.footer-rule{position:absolute;left:98px;top:499px;width:1004px;height:1px;background:rgba(255,255,255,.3)}
.copyright{position:absolute;left:98px;top:528px;font-size:11.5px}
.social{position:absolute;left:953px;top:524px;display:flex;gap:18px}
.social span{width:26px;height:26px;background:var(--white);border-radius:4px}
</style>
</head>
<body>

<section class="hero">
  <div class="hero-photo" role="img" aria-label="Plate of spaghetti with tomato sauce and basil on a wooden table"></div>
  <div class="hero-panel"></div>
  <div class="brand"><span class="brand-dot"></span><span class="brand-name">TEATRO LUCERNA</span></div>
  <div class="brand-sub">Ristorante Italiano</div>
  <div class="top-contact">
    <span class="phone">
      <svg width="16" height="16" viewBox="0 0 24 24" fill="#fff"><path d="M6.6 10.8a15 15 0 0 0 6.6 6.6l2.2-2.2c.3-.3.7-.4 1-.2 1.1.4 2.3.6 3.6.6.6 0 1 .4 1 1V20c0 .6-.4 1-1 1A17 17 0 0 1 3 4c0-.6.4-1 1-1h3.5c.6 0 1 .4 1 1 0 1.3.2 2.5.6 3.6.1.3 0 .7-.2 1z"/></svg>
      (+31) 20 555 0192
    </span>
    <span class="menu-btn"><svg width="18" height="14" viewBox="0 0 18 14" fill="#fff"><rect width="18" height="2.4"/><rect y="5.8" width="18" height="2.4"/><rect y="11.6" width="18" height="2.4"/></svg></span>
  </div>
  <h1 class="hero-title">TEATRO<br>LUCERNA</h1>
  <p class="hero-lead">We are an Italian restaurant<br>from Amsterdam</p>
  <span class="btn-outline">Reserve a table</span>
  <div class="dots"><span></span><span></span><span></span><span></span></div>
</section>

<section class="announce">NOW OPEN ON SUNDAYS !</section>

<section class="story">
  <div class="story-text">
    <div class="kicker">Italian restaurant</div>
    <h2 class="section-title">OUR STORY</h2>
    <p>At vero eos et accusamus et iusto odio dignissimos ducimus<br>qui bian ditiis praesentium voluptatum deleniti atque corrupti qu<br>os dolores et quas molestias excepturi sint occaecati cupiditate<br>non provid Ipa qui officia deserunt mollitia ani</p>
    <span class="btn-solid">Read more</span>
  </div>
  <div class="photo photo-a" role="img" aria-label="Grilled lobster on a plate"></div>
  <div class="photo photo-b" role="img" aria-label="Bottle of red wine on a table"></div>
  <div class="photo photo-c" role="img" aria-label="Tomato and basil starter on a white plate"></div>
</section>

<section class="about">
  <div class="about-card">
    <div class="about-photo" role="img" aria-label="Plated dish with green asparagus and olive oil"></div>
    <div class="about-body">
      <h2 class="section-title">ABOUT TEATRO LUCERNA</h2>
      <p>At vero eos et accusamus et iusto odio dignissimos ducimus qui blanditiis praesentium voluptatum deleniti atque corrupti quos dolor.</p>
      <p>Quas molestias excepturi sint occaecati cupiditate non provident, similique sunt incul pa qui officia deserunt mollitia animi, id est laborum et dolorum fuga. Et harum qiem rerum facilis est et expedita distinctio. Nam libero tempore, cum soluta nobis est elig endi optio cumque nihil impedit quo minus id quod.</p>
      <span class="btn-solid">Read more</span>
    </div>
  </div>
</section>

<section class="menu">
  <h2 class="section-title">MENU</h2>
  <div class="menu-card left">
    <div class="menu-photo" role="img" aria-label="Bruschetta with diced tomatoes"></div>
    <h3>MENU (NEW)</h3>
    <ul>
      <li><svg width="11" height="9" viewBox="0 0 11 9"><path d="M1 4.5l3 3 6-6" stroke="#a14a5c" stroke-width="2.2" fill="none"/></svg>Antipasti</li>
      <li><svg width="11" height="9" viewBox="0 0 11 9"><path d="M1 4.5l3 3 6-6" stroke="#a14a5c" stroke-width="2.2" fill="none"/></svg>Le Insalate</li>
      <li><svg width="11" height="9" viewBox="0 0 11 9"><path d="M1 4.5l3 3 6-6" stroke="#a14a5c" stroke-width="2.2" fill="none"/></svg>Le Paste</li>
      <li><svg width="11" height="9" viewBox="0 0 11 9"><path d="M1 4.5l3 3 6-6" stroke="#a14a5c" stroke-width="2.2" fill="none"/></svg>Il Pesce</li>
    </ul>
  </div>
  <div class="menu-card right">
    <div class="menu-photo" role="img" aria-label="Caprese salad with mozzarella and tomato"></div>
    <h3>GROUP MENU</h3>
    <ul>
      <li><svg width="11" height="9" viewBox="0 0 11 9"><path d="M1 4.5l3 3 6-6" stroke="#a14a5c" stroke-width="2.2" fill="none"/></svg>Antipasti</li>
      <li><svg width="11" height="9" viewBox="0 0 11 9"><path d="M1 4.5l3 3 6-6" stroke="#a14a5c" stroke-width="2.2" fill="none"/></svg>Secondi</li>
      <li><svg width="11" height="9" viewBox="0 0 11 9"><path d="M1 4.5l3 3 6-6" stroke="#a14a5c" stroke-width="2.2" fill="none"/></svg>Dolci</li>
      <li><svg width="11" height="9" viewBox="0 0 11 9"><path d="M1 4.5l3 3 6-6" stroke="#a14a5c" stroke-width="2.2" fill="none"/></svg>Il Pesce</li>
    </ul>
  </div>
</section>

<section class="features">
  <div class="feature">
    <span class="feature-icon"><svg width="38" height="38" viewBox="0 0 24 24" fill="none" stroke="#a14a5c" stroke-width="2"><rect x="3" y="5" width="18" height="16" rx="1"/><path d="M3 10h18M8 3v4M16 3v4"/><path d="M7 13h2M11 13h2M15 13h2M7 17h2M11 17h2M15 17h2"/></svg></span>
    <h3>RESERVATION</h3>
    <p>Tables can be reserved online through our website</p>
    <span class="btn-outline">Reserve a table</span>
  </div>
  <div class="feature">
    <span class="feature-icon"><svg width="38" height="38" viewBox="0 0 24 24" fill="none" stroke="#a14a5c" stroke-width="2"><rect x="3" y="4" width="18" height="16" rx="1"/><circle cx="8.5" cy="9" r="1.6" fill="#a14a5c"/><path d="M4 18l5-5 3 3 4-5 4 5" fill="#a14a5c"/></svg></span>
    <h3>Portfolio</h3>
    <p>Tables can be reserved online through our website</p>
    <span class="btn-outline">View gallery</span>
  </div>
  <div class="feature">
    <span class="feature-icon"><svg width="40" height="40" viewBox="0 0 24 24" fill="#a14a5c"><path d="M3 4h11a2 2 0 0 1 2 2v5a2 2 0 0 1-2 2H8l-4 3v-3H3a2 2 0 0 1-2-2V6a2 2 0 0 1 2-2z"/><path d="M18 8h3a2 2 0 0 1 2 2v5a2 2 0 0 1-2 2h-1v3l-4-3h-5a2 2 0 0 1-2-2v-1h6a3 3 0 0 0 3-3z"/></svg></span>
    <h3>Blog</h3>
    <p>Tables can be reserved online through our website</p>
    <span class="btn-outline">View blog</span>
  </div>
  <span class="divider" style="left:437px"></span>
  <span class="divider" style="left:803px"></span>
</section>

<section class="contact">
  <h2 class="section-title">CONTACT US</h2>
  <div class="col-title" style="left:98px;top:141px">Contact form</div>
  <div class="field-label" style="left:100px;top:182px">Name :</div>
  <div class="field-label" style="left:419px;top:182px">Phone no :</div>
  <div class="field" style="left:100px;top:203px;width:311px;height:33px"></div>
  <div class="field" style="left:419px;top:203px;width:311px;height:33px"></div>
  <div class="field-label" style="left:100px;top:252px">Email :</div>
  <div class="field" style="left:100px;top:268px;width:630px;height:33px"></div>
  <div class="field-label" style="left:100px;top:319px">Message :</div>
  <div class="field" style="left:100px;top:336px;width:630px;height:81px"></div>
  <span class="btn-solid submit">Submit</span>

  <div class="col-title" style="left:809px;top:141px">Contact information</div>
  <div class="info-item" style="top:176px">
    <span class="info-icon"><svg width="14" height="16" viewBox="0 0 24 24" fill="#fff"><path d="M12 2a7 7 0 0 0-7 7c0 5 7 13 7 13s7-8 7-13a7 7 0 0 0-7-7zm0 9.5A2.5 2.5 0 1 1 12 6.5a2.5 2.5 0 0 1 0 5z"/></svg></span>
    <span>Lindengracht 42<br>1015 KK Amsterdam</span>
  </div>
  <div class="info-item" style="top:234px">
    <span class="info-icon"><svg width="15" height="12" viewBox="0 0 24 18" fill="#fff"><path d="M0 0h24v2L12 10 0 2z"/><path d="M0 5l12 8 12-8v13H0z"/></svg></span>
    <span>info@teatrolucerna.info</span>
  </div>
  <div class="info-item" style="top:290px">
    <span class="info-icon"><svg width="14" height="14" viewBox="0 0 24 24" fill="#fff"><path d="M6.6 10.8a15 15 0 0 0 6.6 6.6l2.2-2.2c.3-.3.7-.4 1-.2 1.1.4 2.3.6 3.6.6.6 0 1 .4 1 1V20c0 .6-.4 1-1 1A17 17 0 0 1 3 4c0-.6.4-1 1-1h3.5c.6 0 1 .4 1 1 0 1.3.2 2.5.6 3.6.1.3 0 .7-.2 1z"/></svg></span>
    <span>+31 20 555 0192</span>
  </div>
  <div class="col-title" style="left:809px;top:357px">Opening hours</div>
  <div class="hours">
    <div><span>Monday -</span><span>Closed</span></div>
    <div><span>Tuesday, Thursday</span><span>18:00 - 23:00</span></div>
    <div><span>Sunday</span><span>Closed</span></div>
  </div>

  <div class="footer-rule"></div>
  <div class="copyright">Copyrights © 2018, Teatro Lucerna . All Rights Reserved.</div>
  <div class="social"><span></span><span></span><span></span><span></span></div>
</section>

</body>
</html>
```